Bram Keystone Homes needs a business card

We need a business card for a new company in Canada, Ontario. Our company is all about luxury contraction homes for our clients. Our product and services are custom projects design. Under the business logo that will be created, we want a slogan that will be a memorable phrase for consumers to remember us to tell their friends and relatives.

Additional infomation
- Ludovic Entrasse
- President / Ceo
-519.604.3087

Find point what luxury construction products and services can be done

We like to see colors:
- #663300
- and something other colors or color that would attract the client needs and wants

The final design should communicate leads from new or old clients that will grow our empire. Most of all, we try to work among the budget that clients want

NOTE
- we also need an icon for the business (Example: Instagram, Facebook, and Whatsapp icons)
- We want the company name to be remembered easily for clients and our distributors who would get our orders.
- we need an icon on the business cards: Facebook and Instagram.

Thanks,
Bram Keystone Homes

```html
<!DOCTYPE html>
<html lang="en">
<head>
<meta charset="utf-8">
<title>Bram Keystone Homes — Business Card</title>
<link rel="stylesheet" href="https://fonts.googleapis.com/css2?family=Poppins:wght@400;500;800&display=swap">
<style>
  :root {
    --brand-brown: #663300;
    --card-white: #ffffff;
    --backdrop: #222222;
    --ink-light: #ffffff;
  }
  * { box-sizing: border-box; margin: 0; padding: 0; }
  html, body {
    width: 1200px; height: 874px; overflow: hidden;
    background: var(--backdrop);
    font-family: "Poppins", sans-serif;
  }
  .stage {
    width: 1200px; height: 874px;
    display: flex; flex-direction: column; align-items: center; justify-content: center;
    gap: 26px;
  }
  .card {
    width: 620px; height: 354px;
    position: relative; overflow: hidden;
    box-shadow: 0 10px 28px rgba(0,0,0,.45);
  }
  .card-front {
    background: var(--brand-brown);
    color: var(--ink-light);
    display: flex; flex-direction: column; align-items: center; justify-content: center;
  }
  .wordmark {
    font-weight: 800; font-size: 44px; line-height: 1; letter-spacing: -0.5px;
  }
  .tagline {
    font-weight: 500; font-size: 15px; letter-spacing: 0.4px; margin-top: 6px;
    text-transform: uppercase;
  }
  .social-row { display: flex; gap: 6px; margin-top: 40px; }
  .social-dot { width: 30px; height: 30px; }

  .card-back { background: var(--card-white); }
  .back-brand {
    position: absolute; top: 0; left: 0; right: 0; height: 232px;
    display: flex; flex-direction: column; align-items: center; justify-content: center;
    color: var(--brand-brown);
  }
  .back-brand .wordmark { font-size: 32px; }
  .back-brand .tagline { font-size: 11px; margin-top: 4px; }
  .contact-band {
    position: absolute; left: 0; right: 0; bottom: 0; height: 122px;
    background: var(--brand-brown); color: var(--ink-light);
    display: flex; align-items: center; justify-content: center; gap: 26px;
  }
  .person { text-align: right; }
  .person-name { font-weight: 500; font-size: 23px; line-height: 1.2; }
  .person-role { font-weight: 400; font-size: 17px; }
  .divider { width: 2px; height: 66px; background: var(--ink-light); }
  .phone { font-weight: 500; font-size: 22px; letter-spacing: 0.5px; margin-top: 22px; }
</style>
</head>
<body>
<main class="stage">
  <section class="card card-front">
    <div class="wordmark">Bram Keystone Homes</div>
    <div class="tagline">- Home Renovations - Custom Project Design -</div>
    <div class="social-row" aria-label="Social media links">
      <svg class="social-dot" viewBox="0 0 30 30" aria-hidden="true"><circle cx="15" cy="15" r="13" fill="none" stroke="#fff" stroke-width="1.5"/></svg>
      <svg class="social-dot" viewBox="0 0 30 30" aria-hidden="true"><circle cx="15" cy="15" r="13" fill="none" stroke="#fff" stroke-width="1.5"/></svg>
      <svg class="social-dot" viewBox="0 0 30 30" aria-hidden="true"><circle cx="15" cy="15" r="13" fill="none" stroke="#fff" stroke-width="1.5"/></svg>
    </div>
  </section>

  <section class="card card-back">
    <div class="back-brand">
      <div class="wordmark">Bram Keystone Homes</div>
      <div class="tagline">- Home Renovations - Custom Project Design -</div>
    </div>
    <div class="contact-band">
      <div class="person">
        <div class="person-name">Ludovic Entrasse</div>
        <div class="person-role">President / Ceo</div>
      </div>
      <div class="divider"></div>
      <div class="phone">519.604.3087</div>
    </div>
  </section>
</main>
</body>
</html>
```